Business Card Design Project

We have recently completed CraftHive projects for a new logo and wesbite.
We now require new business cards.
We hand out very little printed material to clients as all information is online. When we do hand out something, like a business card, we want it to have real impact and make a statement about the quality and professionalism of our company.
We have an idea of what we want our card to look like but we want a designer to make sure they have impact and look great.
Our requirements are…
Size: 85mm X 55mm - Landscape
Front of card: Logo plus the following contact information.
Dennis Marlow
Operations Manager
Phone +44(0) 1632 xxx xxx
Mobile +44(0) 7700 xxx xxx
Email denmo@korvantix.example
Address 17 Pellick Row, Aberdeen AB12 9QZ
Website www.korvantix.example
How you layout the front of the card is up to you, we would like to see some different ideas. Attached are two versions of our logo that may be used.
Back of card: We would like this to be simple but again have impact. Our current thought is to have the logo or just the large W design from the logo in white against a dark background, perhaps made up from the dark green in the logo.
The logos are attached so you can see the colours in them but the dark ones are..
Dark Blue = C:88, M:55, Y:44, K:28
Dark Green = C:87, M:53, Y:50, K:50
We sometimes also use a bright orange as an accent or highlight colour…
Orange: = C:0, M:39, Y:94, K:0

```html
<!DOCTYPE html>
<html lang="en">
<head>
<meta charset="utf-8">
<title>Korvantix Business Card</title>
<link href="https://fonts.googleapis.com/css2?family=Lato:wght@400;700&display=swap" rel="stylesheet">
<style>
  :root {
    --bg: #c9d3d6;
    --ink: #2b2f33;
    --teal-dark: #2d5260;
    --teal: #3c6f7b;
    --teal-light: #6fa7ad;
    --olive: #8c9d4c;
    --white: #ffffff;
  }
  * { margin: 0; padding: 0; box-sizing: border-box; }
  html, body { width: 1200px; height: 960px; overflow: hidden; }
  body {
    background: var(--bg);
    font-family: "Lato", Arial, sans-serif;
    position: relative;
  }
  .card {
    position: absolute;
    width: 640px;
    height: 414px;
    box-shadow: 0 10px 30px rgba(30, 50, 60, 0.25);
    overflow: hidden;
  }
  .card-front { left: 110px; top: 50px; background: var(--white); }
  .card-back {
    left: 450px; top: 500px;
    background: var(--teal-dark);
  }

  .name-line {
    position: absolute; left: 40px; top: 70px;
    display: flex; align-items: baseline; gap: 10px;
    color: var(--ink);
  }
  .person-name { font-size: 30px; font-weight: 400; letter-spacing: 0.5px; }
  .divider { font-size: 26px; }
  .job-title { font-size: 15px; letter-spacing: 0.5px; }

  .contact-list {
    position: absolute; left: 40px; top: 140px;
    list-style: none; font-size: 16px; color: var(--ink);
    line-height: 24px;
  }
  .contact-list li { display: flex; }
  .contact-label { width: 32px; color: var(--teal-dark); }

  .address-block {
    position: absolute; left: 380px; top: 128px;
    font-size: 15px; line-height: 21px; color: var(--ink);
  }
  .address-web { color: var(--teal-dark); font-weight: 700; }

  .brand {
    position: absolute; left: 40px; top: 268px;
    display: flex; align-items: center; gap: 14px;
  }
  .brand-mark {
    width: 46px; height: 46px; border-radius: 50%;
    background: var(--teal);
  }
  .brand-name {
    font-size: 38px; font-weight: 700; color: var(--teal-dark);
    letter-spacing: 1px;
  }

  .front-band {
    position: absolute; left: 0; right: 0; bottom: 0; height: 22px;
    background: linear-gradient(90deg, var(--teal-light) 0%, var(--teal) 45%, var(--olive) 80%, var(--teal-dark) 100%);
  }

  .back-decoration {
    position: absolute; inset: 0;
    background: radial-gradient(ellipse at 60% 60%, rgba(111,167,173,0.45) 0%, rgba(45,82,96,0) 60%),
                linear-gradient(135deg, var(--teal-dark) 0%, var(--teal) 60%, #4a6e5c 100%);
  }
  .back-web {
    position: absolute; left: 0; right: 0; top: 160px;
    text-align: center; color: var(--white);
    font-size: 22px; letter-spacing: 2px;
  }
</style>
</head>
<body>
  <section class="card card-front">
    <div class="name-line">
      <span class="person-name">DENNIS MARLOW</span>
      <span class="divider">|</span>
      <span class="job-title">OPERATIONS MANAGER</span>
    </div>
    <ul class="contact-list">
      <li><span class="contact-label">t</span>+44(0) 1632 xxx xxx</li>
      <li><span class="contact-label">m</span>+44(0) 7700 xxx xxx</li>
      <li><span class="contact-label">e</span>denmo@korvantix.example</li>
    </ul>
    <div class="address-block">
      <p>17 Pellick Row,</p>
      <p>Aberdeen AB12 9QZ</p>
      <p class="address-web">www.korvantix.example</p>
    </div>
    <div class="brand">
      <span class="brand-mark"></span>
      <span class="brand-name">KORVANTIX</span>
    </div>
    <div class="front-band"></div>
  </section>

  <section class="card card-back">
    <div class="back-decoration" role="img" aria-label="Large sweeping brand swoosh in light teal and olive on dark teal"></div>
    <p class="back-web">www.korvantix.example</p>
  </section>
</body>
</html>
```